Redesign Website - Current one too plain

The description is in the uploaded file. Please let me know if you need any more information. I'd prefer it if someone could implement the design to a WordPress site but the best design will win, regardless.
I would like the forms to look nice as well
UPDATE:
I don't think we can use the images that I provided, I think they make the site look a bit 'cheap' and I really don't know how to replace them. One thought I have had is to make the "Simple, Unique, Effective" a second feature on the right side of the page with the search on the left
Target Market(s)
Small companies, private sellers of cars and people who rent their caravan/holiday home out
Industry/Entity Type
Advertising
Number of Pages Required
3 page
Colors
Designer to choose colors to be used in the design.
Look and feel
Each slider illustrates characteristics of the customer's brand and the style your logo design should communicate.

```html
<!DOCTYPE html>
<html lang="en">
<head>
<meta charset="utf-8">
<title>PLAKO – Homepage Concepts</title>
<link href="https://fonts.googleapis.com/css2?family=Poppins:wght@400;500;600;700&display=swap" rel="stylesheet">
<style>
:root{
  --navy:#0b1446;
  --yellow:#fff200;
  --blue:#1fa0e6;
  --blue-light:#d3ebf8;
  --ring:#2aa3e4;
  --ink:#1b1b1b;
  --muted:#555;
  --field:#c9c9c9;
  --footer-dark:#8a8a8a;
  --footer-light:#d4d4d4;
}
*{box-sizing:border-box;margin:0;padding:0}
html,body{width:975px;height:1200px;overflow:hidden;background:#fff}
body{font-family:"Poppins",sans-serif;color:var(--ink)}
.stage{position:absolute;left:0;top:0;width:1736px;height:2140px;transform:scale(.5616);transform-origin:0 0}
.page{position:absolute;top:34px;width:819px;height:2068px;background:#fff;overflow:hidden}
.page--dark{left:29px}
.page--light{left:889px}
.abs{position:absolute}

/* hero */
.hero{left:0;top:0;width:819px;height:456px}
.page--dark .hero{background:var(--navy)}
.page--light .hero{background:linear-gradient(180deg,#fafafa 0%,#eeeeee 50%,#d6d6d6 100%)}
.hero-photo{left:50px;top:150px;width:740px;height:240px;border-radius:40px;background:linear-gradient(90deg,rgba(40,52,100,.35),rgba(30,40,90,.15),rgba(40,52,100,.35))}
.brand{display:flex;align-items:center;gap:12px;font-weight:600;font-size:30px;letter-spacing:8px;color:var(--yellow)}
.brand-dot{width:30px;height:30px;border-radius:50%;background:var(--yellow)}
.brand.top{left:66px;top:18px}
.nav{top:31px;display:flex;gap:31px;font-size:10px;letter-spacing:.3px;left:378px}
.page--dark .nav{color:#fff}
.page--light .nav{color:#333}
.btn{display:flex;align-items:center;justify-content:center;background:var(--yellow);border-radius:20px;font-weight:700;color:var(--navy)}
.btn-login{left:673px;top:19px;width:78px;height:36px;font-size:10px}

.hero-title{font-weight:500;color:#fff;font-size:98px;letter-spacing:2px;line-height:1}
.page--dark .hero-title{left:0;width:819px;text-align:center;top:86px}
.page--light .hero-title{left:98px;top:140px;font-size:52px;color:var(--navy);letter-spacing:1px}
.welcome{left:99px;top:112px;font-size:14px;color:var(--navy)}

.search{display:flex;align-items:center;border:2px solid var(--yellow);border-radius:20px;padding-left:20px;font-size:10px;font-weight:700}
.search .go{position:absolute;right:2px;top:50%;transform:translateY(-50%);width:30px;height:30px;border-radius:50%;background:var(--yellow);display:flex;align-items:center;justify-content:center}
.page--dark .search{left:271px;top:202px;width:275px;height:37px;color:#fff}
.page--light .search{left:97px;top:276px;width:159px;height:37px;color:var(--navy);background:rgba(255,255,255,.5)}
.code-box{display:flex;align-items:center;justify-content:center;gap:8px;font-size:24px}
.page--dark .code-box{border:1.5px solid #fff;color:#fff;top:261px;height:41px}
.page--light .code-box{border:1.5px solid var(--yellow);color:var(--navy);top:212px;height:42px}
.arrows-ud{font-size:10px;line-height:8px;display:flex;flex-direction:column}
.dots{display:flex;gap:6px}
.dots span{width:8px;height:8px;border-radius:50%;background:#fff}
.dots span.on{background:var(--yellow)}

.car-photo{left:380px;top:140px;width:360px;height:170px;border-radius:30px;background:linear-gradient(180deg,#9d9d9d,#6e6e6e);box-shadow:0 0 0 60px rgba(255,242,0,.12)}
.badge{left:526px;top:104px;width:44px;height:44px;border-radius:50%;background:var(--yellow);font-weight:600;font-size:13px;display:flex;align-items:center;justify-content:center;color:var(--navy)}

/* features */
.features{left:66px;top:380px;width:686px;height:222px;background:#fff;border-radius:14px;box-shadow:0 4px 14px rgba(0,0,0,.12)}
.feature{position:absolute;top:43px;width:170px;text-align:center}
.feature-icon{width:70px;height:70px;margin:0 auto;border:1.5px solid var(--ring);border-radius:50%;display:flex;align-items:center;justify-content:center}
.feature h3{margin-top:12px;font-size:12px;font-weight:700}
.feature p{margin-top:7px;font-size:8.5px;line-height:15px;color:var(--muted)}
.flow{position:absolute;top:70px}

/* about */
.about-photo{left:86px;top:688px;width:289px;height:334px;border-radius:46% 54% 40% 60% / 55% 45% 55% 45%;background:linear-gradient(160deg,#dfe6ee 0%,#a9b1ba 45%,#8c7458 100%)}
.section-title{font-weight:700;font-size:24px;color:var(--ink)}
.about-title{left:408px;top:676px}
.about-text{left:408px;width:322px;font-size:9.2px;line-height:18.4px;color:#333;text-align:justify}
.btn-more{left:409px;top:966px;width:97px;height:36px;font-size:9.5px}

/* testimonials */
.testimonials{left:0;top:1084px;width:819px;height:332px}
.page--dark .testimonials{background:var(--blue)}
.page--light .testimonials{background:var(--blue-light)}
.testi-title{left:0;width:819px;text-align:center;top:1138px}
.page--dark .testi-title{color:#fff}
.avatar{left:133px;top:1229px;width:98px;height:98px;border-radius:50%;border:3px solid #fff;background:linear-gradient(180deg,#c8b59b,#7a6650)}
.stars{left:303px;top:1207px;color:#ffc400;font-size:11px;letter-spacing:1px}
.quote{left:265px;top:1222px;font-size:46px;font-weight:700;line-height:1}
.page--dark .quote{color:rgba(255,255,255,.35)}
.page--light .quote{color:#7fc2ea}
.testi-text{left:303px;top:1235px;width:395px;font-size:9.5px;line-height:17px}
.testi-name{left:303px;top:1297px;font-size:12px;font-weight:600}
.testi-role{left:303px;top:1318px;font-size:8.5px}
.page--dark .testi-text,.page--dark .testi-name,.page--dark .testi-role{color:#fff}
.page--light .testi-text,.page--light .testi-name,.page--light .testi-role{color:#222}

/* contact */
.contact-title{left:0;width:819px;text-align:center;top:1490px;font-size:26px}
.field{height:40px;border:1px solid var(--field);border-radius:20px;box-shadow:0 2px 4px rgba(0,0,0,.12);padding-left:18px;display:flex;align-items:center;font-size:10px;color:#555;background:#fff}
.btn-submit{left:350px;top:1738px;width:118px;height:39px;font-weight:400;font-size:12px;color:var(--navy)}

/* footer */
.footer{left:0;top:1859px;width:819px;height:209px}
.page--dark .footer{background:var(--footer-dark)}
.page--light .footer{background:var(--footer-light)}
.brand.bottom{left:0;width:819px;justify-content:center;top:1902px;font-size:32px}
.foot-nav{left:0;width:819px;top:1957px;display:flex;justify-content:center;gap:37px;font-size:9.5px}
.page--dark .foot-nav,.page--dark .copy{color:#fff}
.page--light .foot-nav,.page--light .copy{color:#333}
.socials{left:0;width:819px;top:1993px;display:flex;justify-content:center;gap:5px}
.socials span{width:21px;height:21px;border-radius:50%;border:1.2px solid #fff}
.copy{left:0;width:819px;text-align:center;top:2029px;font-size:9.5px}
</style>
</head>
<body>
<div class="stage">

<!-- ===== Dark concept ===== -->
<section class="page page--dark">
  <div class="abs hero"></div>
  <div class="abs hero-photo" role="img" aria-label="Dimmed photo of parked cars and a van"></div>
  <div class="abs brand top"><span class="brand-dot"></span>PLAKO</div>
  <nav class="abs nav"><span>HOME</span><span>ADVERTISE</span><span>CONTACT</span><span>REGISTER</span></nav>
  <div class="abs btn btn-login">LOG IN</div>
  <h1 class="abs hero-title">PLAKO</h1>
  <div class="abs search">CAR &nbsp;⌄<span class="go"><svg width="11" height="11" viewBox="0 0 12 12"><circle cx="5" cy="5" r="3.5" fill="none" stroke="#0b1446" stroke-width="1.6"/><line x1="7.6" y1="7.6" x2="11" y2="11" stroke="#0b1446" stroke-width="1.6"/></svg></span></div>
  <div class="abs code-box" style="left:344px;width:59px">A<span class="arrows-ud">▲<br>▼</span></div>
  <div class="abs code-box" style="left:416px;width:58px">1<span class="arrows-ud">▲<br>▼</span></div>
  <div class="abs dots" style="left:390px;top:347px"><span></span><span class="on"></span><span></span></div>

  <div class="abs features">
    <div class="feature" style="left:40px">
      <div class="feature-icon"><svg width="36" height="24" viewBox="0 0 36 24"><rect x="2" y="4" width="28" height="16" rx="2" fill="none" stroke="#fff200" stroke-width="2"/><line x1="30" y1="10" x2="34" y2="10" stroke="#fff200" stroke-width="2"/><line x1="30" y1="15" x2="34" y2="15" stroke="#fff200" stroke-width="2"/></svg></div>
      <h3>Simple</h3><p>create &nbsp;your advert and display<br>your code</p></div>
    <svg class="flow" style="left:208px" width="64" height="20" viewBox="0 0 64 20"><path d="M2 6 Q30 26 60 6" fill="none" stroke="#777"/><path d="M55 5 L60 6 L58 10" fill="none" stroke="#777"/></svg>
    <div class="feature" style="left:258px">
      <div class="feature-icon"><svg width="34" height="34" viewBox="0 0 34 34"><circle cx="20" cy="13" r="8" fill="none" stroke="#fff200" stroke-width="2"/><line x1="14" y1="19" x2="5" y2="29" stroke="#fff200" stroke-width="3"/></svg></div>
      <h3>Unique</h3><p>customers find you by an easy-to-re-<br>member code</p></div>
    <svg class="flow" style="left:418px" width="64" height="20" viewBox="0 0 64 20"><path d="M2 14 Q30 -6 60 14" fill="none" stroke="#777"/><path d="M55 14 L60 14 L59 9" fill="none" stroke="#777"/></svg>
    <div class="feature" style="left:476px">
      <div class="feature-icon"><svg width="28" height="34" viewBox="0 0 28 34"><rect x="3" y="2" width="22" height="30" rx="2" fill="none" stroke="#fff200" stroke-width="2"/><line x1="8" y1="10" x2="20" y2="10" stroke="#fff200" stroke-width="1.6"/><line x1="8" y1="16" x2="20" y2="16" stroke="#fff200" stroke-width="1.6"/><line x1="8" y1="22" x2="20" y2="22" stroke="#fff200" stroke-width="1.6"/></svg></div>
      <h3>Effective</h3><p>customers are directed to you and not<br>a list of your competitors</p></div>
  </div>

  <div class="abs about-photo" role="img" aria-label="Silver hatchback photo inside a splash shape"></div>
  <h2 class="abs section-title about-title">ABOUT PLAKO</h2>
  <p class="abs about-text" style="top:730px">Lorem ipsum dolor sit amet, consectetur adipiscing elit, sed do eiusmod tempor incididunt ut labore et dolore magna aliqua. Ut enim ad minim veniam, quis nostrud exercitation ullamco laboris nisi ut aliquip ex ea commodo consequat. Duis aute irure dolor in reprehenderit in voluptate velit esse cillum dolore eu fugiat nulla pariatur. Excepteur sint occaecat cupidatat non proident, sunt in culpa qui officia deserunt mollit anim id est laborum.</p>
  <p class="abs about-text" style="top:872px">Lorem ipsum dolor sit amet, consectetur adipiscing elit, sed do eiusmod tempor incididunt ut labore et dolore magna aliqua. Ut enim ad minim veniam, quis nostrud exercitation ullamco laboris nisi ut aliquip ex ea commodo consequat.</p>
  <div class="abs btn btn-more">LEARN MORE</div>

  <div class="abs testimonials" role="img" aria-label="Blue-tinted photo of a caravan"></div>
  <h2 class="abs section-title testi-title">CLIENT TESTIMONIALS</h2>
  <div class="abs avatar" role="img" aria-label="Client portrait"></div>
  <div class="abs stars">★★★★★</div>
  <div class="abs quote">“</div>
  <p class="abs testi-text">Lorem ipsum dolor sit amet, consectetur adipiscing elit, sed do eiusmod tempor incididunt ut labore et dolore magna aliqua. Ut enim ad minim veniam, quis nostrud exercitation ullamco laboris nisi ut aliquip ex ea commodo consequat.</p>
  <div class="abs testi-name">Tomas</div>
  <div class="abs testi-role">Lorem ipsum dolor</div>
  <div class="abs dots" style="left:303px;top:1351px"><span></span><span class="on"></span><span></span><span></span></div>

  <h2 class="abs section-title contact-title">CONTACT US</h2>
  <div class="abs field" style="left:105px;top:1556px;width:297px">First Name :</div>
  <div class="abs field" style="left:415px;top:1556px;width:298px">Last Name :</div>
  <div class="abs field" style="left:105px;top:1612px;width:297px">Email :</div>
  <div class="abs field" style="left:415px;top:1612px;width:298px">Phone :</div>
  <div class="abs field" style="left:105px;top:1672px;width:607px">Message :</div>
  <div class="abs btn btn-submit">SUBMIT</div>

  <footer class="abs footer"></footer>
  <div class="abs brand bottom"><span class="brand-dot"></span>PLAKO</div>
  <nav class="abs foot-nav"><span>HOME</span><span>ADVERTISE</span><span>CONTACT</span><span>REGISTER</span></nav>
  <div class="abs socials"><span></span><span></span><span></span><span></span><span></span></div>
  <div class="abs copy">©Copyrights 2023 Plako &nbsp;| &nbsp;All Rights Reserved</div>
</section>

<!-- ===== Light concept ===== -->
<section class="page page--light">
  <div class="abs hero"></div>
  <div class="abs brand top"><span class="brand-dot"></span>PLAKO</div>
  <nav class="abs nav"><span>HOME</span><span>ADVERTISE</span><span>CONTACT</span><span>REGISTER</span></nav>
  <div class="abs btn btn-login">LOG IN</div>
  <div class="abs welcome">WELCOME TO</div>
  <h1 class="abs hero-title">PLAKO</h1>
  <div class="abs code-box" style="left:98px;width:58px">A<span class="arrows-ud">▲<br>▼</span></div>
  <div class="abs code-box" style="left:170px;width:58px">1<span class="arrows-ud">▲<br>▼</span></div>
  <div class="abs search">CAR &nbsp;⌄<span class="go"><svg width="11" height="11" viewBox="0 0 12 12"><circle cx="5" cy="5" r="3.5" fill="none" stroke="#0b1446" stroke-width="1.6"/><line x1="7.6" y1="7.6" x2="11" y2="11" stroke="#0b1446" stroke-width="1.6"/></svg></span></div>
  <div class="abs car-photo" role="img" aria-label="Silver SUV photo"></div>
  <div class="abs badge">K14</div>
  <svg class="abs" style="left:336px;top:202px" width="30" height="24" viewBox="0 0 30 24"><path d="M28 12 H4 M13 3 L3 12 L13 21" fill="none" stroke="#0b1446" stroke-width="3"/></svg>
  <svg class="abs" style="left:748px;top:202px" width="30" height="24" viewBox="0 0 30 24"><path d="M2 12 H26 M17 3 L27 12 L17 21" fill="none" stroke="#9a9a9a" stroke-width="3"/></svg>
  <div class="abs dots" style="left:390px;top:347px"><span></span><span class="on"></span><span></span></div>

  <div class="abs features">
    <div class="feature" style="left:40px">
      <div class="feature-icon"><svg width="36" height="24" viewBox="0 0 36 24"><rect x="2" y="4" width="28" height="16" rx="2" fill="none" stroke="#fff200" stroke-width="2"/><line x1="30" y1="10" x2="34" y2="10" stroke="#fff200" stroke-width="2"/><line x1="30" y1="15" x2="34" y2="15" stroke="#fff200" stroke-width="2"/></svg></div>
      <h3>Simple</h3><p>create &nbsp;your advert and display<br>your code</p></div>
    <svg class="flow" style="left:208px" width="64" height="20" viewBox="0 0 64 20"><path d="M2 6 Q30 26 60 6" fill="none" stroke="#777"/><path d="M55 5 L60 6 L58 10" fill="none" stroke="#777"/></svg>
    <div class="feature" style="left:258px">
      <div class="feature-icon"><svg width="34" height="34" viewBox="0 0 34 34"><circle cx="20" cy="13" r="8" fill="none" stroke="#fff200" stroke-width="2"/><line x1="14" y1="19" x2="5" y2="29" stroke="#fff200" stroke-width="3"/></svg></div>
      <h3>Unique</h3><p>customers find you by an easy-to-re-<br>member code</p></div>
    <svg class="flow" style="left:418px" width="64" height="20" viewBox="0 0 64 20"><path d="M2 14 Q30 -6 60 14" fill="none" stroke="#777"/><path d="M55 14 L60 14 L59 9" fill="none" stroke="#777"/></svg>
    <div class="feature" style="left:476px">
      <div class="feature-icon"><svg width="28" height="34" viewBox="0 0 28 34"><rect x="3" y="2" width="22" height="30" rx="2" fill="none" stroke="#fff200" stroke-width="2"/><line x1="8" y1="10" x2="20" y2="10" stroke="#fff200" stroke-width="1.6"/><line x1="8" y1="16" x2="20" y2="16" stroke="#fff200" stroke-width="1.6"/><line x1="8" y1="22" x2="20" y2="22" stroke="#fff200" stroke-width="1.6"/></svg></div>
      <h3>Effective</h3><p>customers are directed to you and not<br>a list of your competitors</p></div>
  </div>

  <div class="abs about-photo" role="img" aria-label="Silver hatchback photo inside a splash shape"></div>
  <h2 class="abs section-title about-title">ABOUT PLAKO</h2>
  <p class="abs about-text" style="top:730px">Lorem ipsum dolor sit amet, consectetur adipiscing elit, sed do eiusmod tempor incididunt ut labore et dolore magna aliqua. Ut enim ad minim veniam, quis nostrud exercitation ullamco laboris nisi ut aliquip ex ea commodo consequat. Duis aute irure dolor in reprehenderit in voluptate velit esse cillum dolore eu fugiat nulla pariatur. Excepteur sint occaecat cupidatat non proident, sunt in culpa qui officia deserunt mollit anim id est laborum.</p>
  <p class="abs about-text" style="top:872px">Lorem ipsum dolor sit amet, consectetur adipiscing elit, sed do eiusmod tempor incididunt ut labore et dolore magna aliqua. Ut enim ad minim veniam, quis nostrud exercitation ullamco laboris nisi ut aliquip ex ea commodo consequat.</p>
  <div class="abs btn btn-more">LEARN MORE</div>

  <div class="abs testimonials"></div>
  <h2 class="abs section-title testi-title">CLIENT TESTIMONIALS</h2>
  <div class="abs avatar" role="img" aria-label="Client portrait"></div>
  <div class="abs stars">★★★★★</div>
  <div class="abs quote">“</div>
  <p class="abs testi-text">Lorem ipsum dolor sit amet, consectetur adipiscing elit, sed do eiusmod tempor incididunt ut labore et dolore magna aliqua. Ut enim ad minim veniam, quis nostrud exercitation ullamco laboris nisi ut aliquip ex ea commodo consequat.</p>
  <div class="abs testi-name">Tomas</div>
  <div class="abs testi-role">Lorem ipsum dolor</div>
  <div class="abs dots" style="left:303px;top:1351px"><span></span><span class="on"></span><span></span><span></span></div>

  <h2 class="abs section-title contact-title">CONTACT US</h2>
  <div class="abs field" style="left:105px;top:1556px;width:297px">First Name :</div>
  <div class="abs field" style="left:415px;top:1556px;width:298px">Last Name :</div>
  <div class="abs field" style="left:105px;top:1612px;width:297px">Email :</div>
  <div class="abs field" style="left:415px;top:1612px;width:298px">Phone :</div>
  <div class="abs field" style="left:105px;top:1672px;width:607px">Message :</div>
  <div class="abs btn btn-submit">SUBMIT</div>

  <footer class="abs footer"></footer>
  <div class="abs brand bottom"><span class="brand-dot"></span>PLAKO</div>
  <nav class="abs foot-nav"><span>HOME</span><span>ADVERTISE</span><span>CONTACT</span><span>REGISTER</span></nav>
  <div class="abs socials"><span></span><span></span><span></span><span></span><span></span></div>
  <div class="abs copy">©Copyrights 2023 Plako &nbsp;| &nbsp;All Rights Reserved</div>
</section>

</div>
</body>
</html>
```